Website redesign - vorelmik.com

We are looking to do a full redesign of vorelmik.com. Need a designer to come up overall layout and 3 specific pages and 3 different hero images.
Wireframes for the 3 pages are attached as well as site images. You don't have to follow the wireframes exactly, but instead the wireframe is there to show you the information that needs to be on each page. Feel free to rearrange as needed.
Our target market is self taught engineers. So definitely I want a more casual feel to it. I'm ok with fun bold colors as well. Really like websites that have the infinite scroll look/feel to them.
Looking to find a designer who will produce HTML and potentially even implement the HTML into our site checked in code.
HTML Code should be responsive/mobile first leveraging Bootstrap 4.
Attached files include:
0) Wireframe PDF
https://files.plomwerk.net/d/7Kx2pQmW9zLr4TbN8vYc3HsE5fJ/view?mode=share
1) Vorelmik Images zip 1
https://files.plomwerk.net/d/4Gt8nRvB2wQx6MkZ1pLd9YaC7hU/view?mode=share
2) Vorelmik Images zip 2
https://files.plomwerk.net/d/9Jw3sTcF5yNv1HqX8rKb2ZeM6dP/view?mode=share
Target Market(s)
I sell DIY Waterproof Electronics enclosures. Target audience is self taught DIY engineers
Coding
Coded - Design and coding required
Number of Pages Required
3 page
Colors
Designer to choose colors to be used in the design.
Look and feel

```html
<!DOCTYPE html>
<html lang="en">
<head>
<meta charset="utf-8">
<title>Vorelmik – Home Page Concepts</title>
<link rel="stylesheet" href="https://fonts.googleapis.com/css2?family=Poppins:wght@400;600;700&family=Roboto:ital,wght@0,400;0,500;0,700;1,400&display=swap">
<style>
:root{
  --board:#6b6b6b;
  --white:#ffffff;
  --blue:#0a00f2;
  --lime:#b8cc14;
  --hero:#dcdaf2;
  --soft:#f2f0f2;
  --ink:#151515;
  --muted:#555555;
  --orange:#ff5a1f;
}
*{box-sizing:border-box;margin:0;padding:0}
html,body{width:733px;height:1200px;overflow:hidden}
body{background:var(--board);font-family:Roboto,Arial,sans-serif;color:var(--ink);position:relative}
h1,h2{font-weight:400}

.page{position:absolute;width:349px;background:var(--white);overflow:hidden}
.page--current{left:11px;top:22px;border-top:1.5px solid var(--blue)}
.page--revised{left:373px;top:22px}

/* nav */
.nav{position:relative;height:32px;background:var(--white)}
.page--revised .nav{height:27px}
.brand{position:absolute;left:33px;top:7px;font-family:Poppins,sans-serif;font-weight:700;font-size:14px;color:var(--blue);letter-spacing:-.2px;display:flex;align-items:center;gap:2px}
.page--revised .brand{top:4px;font-size:12.5px}
.brand-dot{width:4px;height:4px;border-radius:50%;background:var(--lime);align-self:flex-start;margin-top:2px}
.nav-links{position:absolute;top:14px;left:122px;display:flex;gap:11px;font-size:4px;color:#333;list-style:none}
.nav-links .is-active{color:var(--blue)}
.page--revised .nav-links{top:11px;left:102px;gap:12px;font-family:Poppins,sans-serif;font-weight:600;font-size:4.2px;color:#111}
.page--revised .nav-links .is-active{color:var(--lime);border-bottom:1px solid var(--lime);padding-bottom:3px}
.nav-actions{position:absolute;top:12px;left:271px;display:flex;gap:2px}
.page--revised .nav-actions{top:9px;left:266px;gap:3px}
.nav-btn{font-size:3.8px;color:var(--white);padding:2.5px 4px;line-height:1}
.nav-btn--in{background:var(--lime)}
.nav-btn--up{background:var(--blue)}
.page--revised .nav-btn{font-family:Poppins,sans-serif;font-weight:700;padding:3px 4px}
.page--revised .nav-btn--in{background:var(--white);color:var(--lime);border:.6px solid var(--lime)}
.page--revised .nav-btn--up{background:var(--lime)}

/* buttons */
.btn{display:inline-flex;align-items:center;gap:2px;background:var(--blue);color:var(--white);font-family:Roboto,Arial,sans-serif;font-weight:700;font-size:4.6px;padding:5px 5px;border:1px solid #5a5aff;line-height:1}
.btn-arrow{width:4px;height:4px}
.btn--lg{font-size:5.6px;padding:5.5px 5px}

/* hero */
.hero{position:relative;height:120px;background:var(--hero)}
.hero-title{position:absolute;left:33px;top:26px;font-family:Poppins,sans-serif;font-weight:700;font-size:10.5px;line-height:12.2px;color:var(--ink)}
.hero-title small{font-family:Roboto,Arial,sans-serif;font-weight:400;font-size:5px}
.hero .btn{position:absolute;left:33px;top:73px}
.hero-photo{position:absolute;left:180px;top:14px;width:138px;height:100px;border-radius:6px;background:linear-gradient(160deg,#8a9a6a 0%,#5c6a4a 35%,#4a4a4f 70%,#2e2e31 100%)}
.hero-arrow{position:absolute;top:53px;width:14px;height:14px;border-radius:50%;background:#3a3a3a;border:1px solid var(--white)}
.hero-arrow--prev{left:9px}.hero-arrow--next{left:326px}
.hero-arrow svg{width:12px;height:12px;display:block}

/* designer intro */
.designer{position:relative;height:120px}
.designer-photo{position:absolute;left:37px;top:22px;width:121px;height:71px;background:linear-gradient(120deg,#7c6a55,#a9a5a0 55%,#2b2b2b);box-shadow:0 1px 4px rgba(0,0,0,.3);border:1.5px solid var(--white)}
.play{position:absolute;left:53px;top:31px;width:14px;height:9px;border-radius:2px;background:#e01010}
.play::after{content:"";position:absolute;left:5.5px;top:2.5px;border-left:4px solid var(--white);border-top:2px solid transparent;border-bottom:2px solid transparent}
.designer-copy{position:absolute;left:179px;top:40px}
.section-title{font-family:Poppins,sans-serif;font-weight:400;font-size:8px;line-height:10.5px;color:var(--ink)}
.section-title b{font-weight:700}
.designer-copy .btn{margin-top:10px}

/* kits */
.kits{position:relative;height:225px;background:var(--soft);text-align:center}
.kits-title{position:absolute;left:0;right:0;top:15px;font-family:Poppins,sans-serif;font-weight:400;font-size:9.2px;line-height:12px}
.kits-title b{font-weight:700}
.kit-card{position:absolute;box-shadow:0 2px 5px rgba(0,0,0,.15)}
.kit-card--outer-l{left:30px;top:74px;width:32px;height:87px;background:linear-gradient(180deg,#e4e2e4,#b08a5c 50%,#d6d3d6)}
.kit-card--side-l{left:59px;top:64px;width:37px;height:105px;background:linear-gradient(180deg,#d3d0d3,#5a5a5e 55%,#d3d0d3)}
.kit-card--outer-r{left:284px;top:74px;width:36px;height:87px;background:linear-gradient(180deg,#e4e2e4,#9b9ba0 50%,#d6d3d6)}
.kit-card--side-r{left:253px;top:64px;width:34px;height:105px;background:linear-gradient(180deg,#d3d0d3,#6a6a6e 55%,#d3d0d3)}
.kit-card--main{left:94px;top:53px;width:161px;height:127px;background:var(--white)}
.kit-photo{position:absolute;left:8px;top:20px;right:8px;bottom:22px;background:linear-gradient(180deg,#6a7a50 0%,#3c3c40 60%,#1d1d1d 100%);border-radius:4px}
.kits-next{position:absolute;left:330px;top:112px;width:9px;height:9px;border-radius:50%;border:.7px solid #999}
.kits .btn{position:absolute;left:152px;top:193px}

/* makers */
.makers{position:relative;height:149px}
.makers-photo{position:absolute;left:33px;top:27px;width:124px;height:96px;background:linear-gradient(135deg,#8b7257,#b49a78 50%,#7d6a55);box-shadow:0 1px 4px rgba(0,0,0,.3);border:1.5px solid var(--white)}
.makers-copy{position:absolute;left:174px;top:30px}
.makers-copy .section-title{font-size:8.5px;line-height:10px}
.features{list-style:none;margin-top:7px}
.features li{font-size:4.3px;line-height:10px;display:flex;align-items:center;gap:3px}
.tick{width:4px;height:4px}
.makers-copy .btn{margin-top:6px}

/* testimonials */
.reviews{position:relative;height:114px;background:var(--blue);color:var(--white)}
.reviews-title{position:absolute;left:0;right:0;top:10px;text-align:center;font-family:Poppins,sans-serif;font-weight:400;font-size:9.2px}
.reviews-title b{font-weight:700}
.quote{position:absolute;top:33px;width:126px;height:51px;background:var(--white);color:var(--ink);padding:6px 4px 0}
.quote--a{left:43px}.quote--b{left:180px}
.quote p{font-size:4.3px;line-height:9px;color:#444}
.quote--a p{font-style:italic}
.quote cite{position:absolute;left:5px;bottom:6px;font-style:normal;font-size:5px;font-weight:500}
.quote::after{content:"";position:absolute;left:0;bottom:-2px;width:78px;height:2px;background:var(--orange)}
.dots{position:absolute;top:96px;left:0;right:0;display:flex;justify-content:center;gap:2.5px}
.dots span{width:3px;height:3px;border-radius:50%;background:var(--white)}
.dots span.is-off{background:transparent;border:.6px solid var(--white)}

/* examples */
.examples{position:relative;height:378px}
.examples-title{position:absolute;left:0;right:0;top:30px;text-align:center;font-family:Poppins,sans-serif;font-weight:400;font-size:9.2px}
.examples-title b{font-weight:700}
.example-grid{position:absolute;left:33px;top:55px;display:grid;grid-template-columns:repeat(3,84px);column-gap:15px;row-gap:20px}
.example-photo{height:72px;border:.6px solid #ccc;background:linear-gradient(165deg,#f4f4f2 0%,#6f7d5a 40%,#3b3b3f 72%,#f4f4f4 100%)}
.example-photo--case{background:linear-gradient(165deg,#f4f4f4 0%,#c2c2c4 35%,#3d3d40 70%,#f4f4f4 100%)}
.example-photo--board{background:linear-gradient(165deg,#f6f6f6 0%,#b88c55 30%,#a47b48 75%,#f6f6f6 100%)}
.example-name{font-size:5px;margin:6px 0 0 7px;color:#222}
.example-sub{font-size:4.2px;margin:2px 0 0 7px;color:var(--muted)}

/* footer */
.footer{position:relative;height:18px;background:var(--blue);color:var(--white);font-size:4.2px}
.footer-copy{position:absolute;left:33px;top:6px}
.footer-follow{position:absolute;left:274px;top:6px;font-weight:700;display:flex;align-items:center;gap:4px}
.footer-follow i{width:3px;height:3px;border-radius:50%;background:var(--white);display:inline-block}
.footer-code{position:absolute;left:334px;top:6px;font-size:3.6px}
</style>
</head>
<body>

<!-- ============ Concept A ============ -->
<section class="page page--current">
  <header class="nav">
    <div class="brand">vorelmik<span class="brand-dot"></span></div>
    <ul class="nav-links"><li class="is-active">GET STARTED</li><li>DESIGNS</li><li>FAQS</li><li>VIDEOS</li><li>CONTACT US</li></ul>
    <div class="nav-actions"><span class="nav-btn nav-btn--in">SIGN IN</span><span class="nav-btn nav-btn--up">SIGN UP</span></div>
  </header>
  <div class="hero">
    <h1 class="hero-title">Waterproof Project Boxes<br>Customized to your Exact<br>Needs. <small>(at a fraction of the price)</small></h1>
    <span class="btn btn--lg">GET STARTED <svg class="btn-arrow" viewBox="0 0 10 10"><circle cx="5" cy="5" r="5" fill="#fff"/><path d="M4 2.8 6.2 5 4 7.2" stroke="#0a00f2" stroke-width="1.4" fill="none"/></svg></span>
    <div class="hero-photo" role="img" aria-label="Assembled electronics mounting kit with controller boards and wiring"></div>
    <span class="hero-arrow hero-arrow--prev"><svg viewBox="0 0 12 12"><path d="M7 3.5 4.5 6 7 8.5" stroke="#fff" stroke-width="1.3" fill="none"/></svg></span>
    <span class="hero-arrow hero-arrow--next"><svg viewBox="0 0 12 12"><path d="M5 3.5 7.5 6 5 8.5" stroke="#fff" stroke-width="1.3" fill="none"/></svg></span>
  </div>
  <div class="designer">
    <div class="designer-photo" role="img" aria-label="Video still of a grey and a black project box mounted outside a brick wall"><span class="play"></span></div>
    <div class="designer-copy">
      <h2 class="section-title"><b>Customize your Project Box</b> using<br>our Designer</h2>
      <span class="btn">GET STARTED <svg class="btn-arrow" viewBox="0 0 10 10"><circle cx="5" cy="5" r="5" fill="#fff"/><path d="M4 2.8 6.2 5 4 7.2" stroke="#0a00f2" stroke-width="1.4" fill="none"/></svg></span>
    </div>
  </div>
  <div class="kits">
    <h2 class="kits-title"><b>Mounting Kits for all thepopular water proof</b><br>project boxes with many sizes to choose from</h2>
    <div class="kit-card kit-card--outer-l" role="img" aria-label="Mounting plate parts"></div>
    <div class="kit-card kit-card--outer-r" role="img" aria-label="Power supply unit"></div>
    <div class="kit-card kit-card--side-l" role="img" aria-label="Stacked board kit"></div>
    <div class="kit-card kit-card--side-r" role="img" aria-label="Side view of a kit"></div>
    <div class="kit-card kit-card--main"><div class="kit-photo" role="img" aria-label="Two-level mounting kit with green terminal blocks"></div></div>
    <span class="kits-next"></span>
    <span class="btn">GET STARTED <svg class="btn-arrow" viewBox="0 0 10 10"><circle cx="5" cy="5" r="5" fill="#fff"/><path d="M4 2.8 6.2 5 4 7.2" stroke="#0a00f2" stroke-width="1.4" fill="none"/></svg></span>
  </div>
  <div class="makers">
    <div class="makers-photo" role="img" aria-label="Mounting plate with boards and screws laid out on a wooden bench"></div>
    <div class="makers-copy">
      <h2 class="section-title"><b>Vorelmik waterproof project boxes<br>were</b> built by makers for makers</h2>
      <ul class="features">
        <li><svg class="tick" viewBox="0 0 10 10"><circle cx="5" cy="5" r="5" fill="#0a00f2"/><path d="M2.8 5.2 4.3 6.6 7.2 3.6" stroke="#fff" stroke-width="1.3" fill="none"/></svg>Design to your specifications</li>
        <li><svg class="tick" viewBox="0 0 10 10"><circle cx="5" cy="5" r="5" fill="#0a00f2"/><path d="M2.8 5.2 4.3 6.6 7.2 3.6" stroke="#fff" stroke-width="1.3" fill="none"/></svg>Maker components: Corvane, Quillboard, Tolvane Power</li>
        <li><svg class="tick" viewBox="0 0 10 10"><circle cx="5" cy="5" r="5" fill="#0a00f2"/><path d="M2.8 5.2 4.3 6.6 7.2 3.6" stroke="#fff" stroke-width="1.3" fill="none"/></svg>Detailed build instructions, videos, walkthroughs</li>
        <li><svg class="tick" viewBox="0 0 10 10"><circle cx="5" cy="5" r="5" fill="#0a00f2"/><path d="M2.8 5.2 4.3 6.6 7.2 3.6" stroke="#fff" stroke-width="1.3" fill="none"/></svg>DIY made to look professional</li>
      </ul>
      <span class="btn">GET STARTED <svg class="btn-arrow" viewBox="0 0 10 10"><circle cx="5" cy="5" r="5" fill="#fff"/><path d="M4 2.8 6.2 5 4 7.2" stroke="#0a00f2" stroke-width="1.4" fill="none"/></svg></span>
    </div>
  </div>
  <div class="reviews">
    <h2 class="reviews-title"><b>What our</b> Customers Have to Say</h2>
    <blockquote class="quote quote--a"><p>"Great work at a reasonable cost.&nbsp; I can't recommend them enough.&nbsp; If you're doing custom boxes for light shows, this is where you go."</p><cite>Marek T</cite></blockquote>
    <blockquote class="quote quote--b"><p>"Fantastic service/product.. whether you simply generate the design and do all of the fabrication yourself or simply order the kits."</p><cite>Luis P</cite></blockquote>
    <div class="dots"><span></span><span class="is-off"></span><span></span></div>
  </div>
  <div class="examples">
    <h2 class="examples-title"><b>See Real Examples</b> From Our Customers</h2>
    <div class="example-grid">
      <figure><div class="example-photo" role="img" aria-label="Customer build with controller boards"></div><p class="example-name">KTR BCX8-72 w/ P16v3 +</p><p class="example-sub">Expansion board</p></figure>
      <figure><div class="example-photo" role="img" aria-label="Customer build with relay boards"></div><p class="example-name">KTR BCX8-72 w/ P16v3 +</p><p class="example-sub">Expansion board</p></figure>
      <figure><div class="example-photo" role="img" aria-label="Customer build with network ports"></div><p class="example-name">KTR BCX8-72 w/ P16v3 +</p><p class="example-sub">Expansion board</p></figure>
      <figure><div class="example-photo example-photo--case" role="img" aria-label="Build with power supply on top"></div><p class="example-name">KTR BCX8-72 w/ P16v3 +</p><p class="example-sub">Expansion board</p></figure>
      <figure><div class="example-photo example-photo--case" role="img" aria-label="Build with power supply, angled view"></div><p class="example-name">KTR BCX8-72 w/ P16v3 +</p><p class="example-sub">Expansion board</p></figure>
      <figure><div class="example-photo example-photo--case" role="img" aria-label="Build with two power supplies"></div><p class="example-name">KTR BCX8-72 w/ P16v3 +</p><p class="example-sub">Expansion board</p></figure>
      <figure><div class="example-photo example-photo--board" role="img" aria-label="Mounting plate with bagged hardware"></div><p class="example-name">KTR BCX8-72 w/ P16v3 +</p><p class="example-sub">Expansion board</p></figure>
      <figure><div class="example-photo" role="img" aria-label="Build with fan and boards"></div><p class="example-name">KTR BCX8-72 w/ P16v3 +</p><p class="example-sub">Expansion board</p></figure>
      <figure><div class="example-photo" role="img" aria-label="Two-level build with small boards"></div><p class="example-name">KTR BCX8-72 w/ P16v3 +</p><p class="example-sub">Expansion board</p></figure>
    </div>
  </div>
  <footer class="footer">
    <span class="footer-copy">© Copyright 2020 @ vorelmik designer</span>
    <span class="footer-follow">Follow Us: <i></i><i></i></span>
    <span class="footer-code">C37</span>
  </footer>
</section>

<!-- ============ Concept B ============ -->
<section class="page page--revised">
  <header class="nav">
    <div class="brand">vorelmik<span class="brand-dot"></span></div>
    <ul class="nav-links"><li class="is-active">ENCLOSURES</li><li>DESIGNS</li><li>FAQS</li><li>VIDEOS</li><li>CONTACT US</li></ul>
    <div class="nav-actions"><span class="nav-btn nav-btn--in">SIGN IN</span><span class="nav-btn nav-btn--up">SIGN UP</span></div>
  </header>
  <div class="hero">
    <h1 class="hero-title">Waterproof Project Boxes<br>Customized to your Exact<br>Needs. <small>(at a fraction of the price)</small></h1>
    <span class="btn btn--lg">GET STARTED <svg class="btn-arrow" viewBox="0 0 10 10"><circle cx="5" cy="5" r="5" fill="#fff"/><path d="M4 2.8 6.2 5 4 7.2" stroke="#0a00f2" stroke-width="1.4" fill="none"/></svg></span>
    <div class="hero-photo" role="img" aria-label="Assembled electronics mounting kit with controller boards and wiring"></div>
    <span class="hero-arrow hero-arrow--prev"><svg viewBox="0 0 12 12"><path d="M7 3.5 4.5 6 7 8.5" stroke="#fff" stroke-width="1.3" fill="none"/></svg></span>
    <span class="hero-arrow hero-arrow--next"><svg viewBox="0 0 12 12"><path d="M5 3.5 7.5 6 5 8.5" stroke="#fff" stroke-width="1.3" fill="none"/></svg></span>
  </div>
  <div class="designer">
    <div class="designer-photo" role="img" aria-label="Video still of a grey and a black project box mounted outside a brick wall"><span class="play"></span></div>
    <div class="designer-copy">
      <h2 class="section-title"><b>Customize your Project Box</b> using<br>our Designer</h2>
      <span class="btn">GET STARTED <svg class="btn-arrow" viewBox="0 0 10 10"><circle cx="5" cy="5" r="5" fill="#fff"/><path d="M4 2.8 6.2 5 4 7.2" stroke="#0a00f2" stroke-width="1.4" fill="none"/></svg></span>
    </div>
  </div>
  <div class="kits">
    <h2 class="kits-title"><b>Mounting Kits for all thepopular water proof</b><br>project boxes with many sizes to choose from</h2>
    <div class="kit-card kit-card--outer-l" role="img" aria-label="Mounting plate parts"></div>
    <div class="kit-card kit-card--outer-r" role="img" aria-label="Power supply unit"></div>
    <div class="kit-card kit-card--side-l" role="img" aria-label="Stacked board kit"></div>
    <div class="kit-card kit-card--side-r" role="img" aria-label="Side view of a kit"></div>
    <div class="kit-card kit-card--main"><div class="kit-photo" role="img" aria-label="Two-level mounting kit with green terminal blocks"></div></div>
    <span class="kits-next"></span>
    <span class="btn">GET STARTED <svg class="btn-arrow" viewBox="0 0 10 10"><circle cx="5" cy="5" r="5" fill="#fff"/><path d="M4 2.8 6.2 5 4 7.2" stroke="#0a00f2" stroke-width="1.4" fill="none"/></svg></span>
  </div>
  <div class="makers">
    <div class="makers-photo" role="img" aria-label="Mounting plate with boards and screws laid out on a wooden bench"></div>
    <div class="makers-copy">
      <h2 class="section-title"><b>Vorelmik waterproof project boxes<br>were</b> built by makers for makers</h2>
      <ul class="features">
        <li><svg class="tick" viewBox="0 0 10 10"><circle cx="5" cy="5" r="5" fill="#0a00f2"/><path d="M2.8 5.2 4.3 6.6 7.2 3.6" stroke="#fff" stroke-width="1.3" fill="none"/></svg>Design to your specifications</li>
        <li><svg class="tick" viewBox="0 0 10 10"><circle cx="5" cy="5" r="5" fill="#0a00f2"/><path d="M2.8 5.2 4.3 6.6 7.2 3.6" stroke="#fff" stroke-width="1.3" fill="none"/></svg>Maker components: Corvane, Quillboard, Tolvane Power</li>
        <li><svg class="tick" viewBox="0 0 10 10"><circle cx="5" cy="5" r="5" fill="#0a00f2"/><path d="M2.8 5.2 4.3 6.6 7.2 3.6" stroke="#fff" stroke-width="1.3" fill="none"/></svg>Detailed build instructions, videos, walkthroughs</li>
        <li><svg class="tick" viewBox="0 0 10 10"><circle cx="5" cy="5" r="5" fill="#0a00f2"/><path d="M2.8 5.2 4.3 6.6 7.2 3.6" stroke="#fff" stroke-width="1.3" fill="none"/></svg>DIY made to look professional</li>
      </ul>
      <span class="btn">GET STARTED <svg class="btn-arrow" viewBox="0 0 10 10"><circle cx="5" cy="5" r="5" fill="#fff"/><path d="M4 2.8 6.2 5 4 7.2" stroke="#0a00f2" stroke-width="1.4" fill="none"/></svg></span>
    </div>
  </div>
  <div class="reviews">
    <h2 class="reviews-title"><b>What our</b> Customers Have to Say</h2>
    <blockquote class="quote quote--a"><p>"Great work at a reasonable cost.&nbsp; I can't recommend them enough.&nbsp; If you're doing custom boxes for light shows, this is where you go."</p><cite>Marek T</cite></blockquote>
    <blockquote class="quote quote--b"><p>"Fantastic service/product.. whether you simply generate the design and do all of the fabrication yourself or simply order the kits."</p><cite>Luis P</cite></blockquote>
    <div class="dots"><span></span><span class="is-off"></span><span></span></div>
  </div>
  <div class="examples">
    <h2 class="examples-title"><b>See Real Examples</b> From Our Customers</h2>
    <div class="example-grid">
      <figure><div class="example-photo" role="img" aria-label="Customer build with controller boards"></div><p class="example-name">KTR BCX8-72 w/ P16v3 +</p><p class="example-sub">Expansion board</p></figure>
      <figure><div class="example-photo" role="img" aria-label="Customer build with relay boards"></div><p class="example-name">KTR BCX8-72 w/ P16v3 +</p><p class="example-sub">Expansion board</p></figure>
      <figure><div class="example-photo" role="img" aria-label="Customer build with network ports"></div><p class="example-name">KTR BCX8-72 w/ P16v3 +</p><p class="example-sub">Expansion board</p></figure>
      <figure><div class="example-photo example-photo--case" role="img" aria-label="Build with power supply on top"></div><p class="example-name">KTR BCX8-72 w/ P16v3 +</p><p class="example-sub">Expansion board</p></figure>
      <figure><div class="example-photo example-photo--case" role="img" aria-label="Build with power supply, angled view"></div><p class="example-name">KTR BCX8-72 w/ P16v3 +</p><p class="example-sub">Expansion board</p></figure>
      <figure><div class="example-photo example-photo--case" role="img" aria-label="Build with two power supplies"></div><p class="example-name">KTR BCX8-72 w/ P16v3 +</p><p class="example-sub">Expansion board</p></figure>
      <figure><div class="example-photo example-photo--board" role="img" aria-label="Mounting plate with bagged hardware"></div><p class="example-name">KTR BCX8-72 w/ P16v3 +</p><p class="example-sub">Expansion board</p></figure>
      <figure><div class="example-photo" role="img" aria-label="Build with fan and boards"></div><p class="example-name">KTR BCX8-72 w/ P16v3 +</p><p class="example-sub">Expansion board</p></figure>
      <figure><div class="example-photo" role="img" aria-label="Two-level build with small boards"></div><p class="example-name">KTR BCX8-72 w/ P16v3 +</p><p class="example-sub">Expansion board</p></figure>
    </div>
  </div>
  <footer class="footer">
    <span class="footer-copy">© Copyright 2020 @ vorelmik designer</span>
    <span class="footer-follow">Follow Us: <i></i><i></i></span>
    <span class="footer-code">C37</span>
  </footer>
</section>

</body>
</html>
```